Clean business card with logo provided

I want a card that will stand out among the masses. I need the color and image to show professionalism and yet have a family appeal showing that I only deal with win/win scenarios. The back of the card will be used to take notes about the individual so I can use that in my database entry. I like modern design but need professionalism in it also. It needs to fit my "clean, safe, and affordable housing" motto. I need to be able to write on the file and update the card details for my employees.

Target Market(s)

Investors looking to make investment income through real estate

Industry/Entity Type

Real Estate

Contact Information for Business Card

Brent Kovalich
blank address, city, st, zip code
480-555-3174
brentkovalich@ridgeworthrentals.example
www.ridgeworthrentals.example

Font styles to use
Sans Serif

Requirements
Must have
• I would like the back of the card to have lines for info. example
• Met/Visited: Date:
• Interets:
Nice to have
• I want the cards color to match the logo background color. Font with details to be san serif and black. I want the card rectangular with square corners. Standard business card size. I would like to see cards designed with both images to see which i prefer more.

```html
<!DOCTYPE html>
<html lang="en">
<head>
<meta charset="utf-8">
<title>Ridgeworth Rentals LLC – Business Card</title>
<link rel="stylesheet" href="https://fonts.googleapis.com/css2?family=Open+Sans:wght@400;600;700&display=swap">
<style>
  :root {
    --brand-cyan: #00b6cd;
    --brand-teal: #1ba8bd;
    --paper: #ffffff;
    --ink: #111111;
    --backdrop: #ecebe8;
  }
  * { box-sizing: border-box; margin: 0; padding: 0; }
  html, body { width: 1200px; height: 900px; overflow: hidden; }
  body {
    background: var(--backdrop);
    font-family: "Open Sans", sans-serif;
    position: relative;
  }
  .card {
    position: absolute;
    background: var(--paper);
    box-shadow: 0 6px 18px rgba(0,0,0,0.18);
    overflow: hidden;
  }
  .card--front { left: 78px; top: 34px; width: 588px; height: 364px; }
  .card--back  { left: 388px; top: 505px; width: 567px; height: 352px; }

  /* Front */
  .brand { position: absolute; left: 44px; top: 34px; }
  .brand__name {
    font-size: 34px; font-weight: 600; color: var(--brand-teal);
    letter-spacing: 0.5px; line-height: 1.1;
  }
  .brand__tagline {
    margin-top: 14px; font-size: 10.5px; color: var(--brand-teal); letter-spacing: 0.2px;
  }
  .front__band {
    position: absolute; left: 0; top: 156px; width: 100%; height: 208px;
    background: var(--brand-cyan); color: var(--paper);
    padding: 14px 31px;
  }
  .holder__name { font-size: 20px; font-weight: 600; line-height: 28px; }
  .holder__address { margin-top: 16px; font-size: 15px; line-height: 18px; }
  .contact { list-style: none; margin-top: 22px; }
  .contact__item {
    display: flex; align-items: center; font-size: 15px; line-height: 25px;
  }
  .contact__icon { width: 12px; height: 12px; margin-right: 11px; fill: var(--paper); flex: none; }

  /* Back */
  .back__band { position: absolute; left: 0; width: 100%; background: var(--brand-cyan); }
  .back__band--top { top: 0; height: 103px; }
  .back__band--bottom { top: 250px; height: 102px; }
  .notes { position: absolute; left: 107px; top: 131px; width: 352px; }
  .notes__row { display: flex; align-items: baseline; height: 41px; }
  .notes__label { font-size: 15.5px; font-weight: 600; color: var(--brand-teal); white-space: nowrap; }
  .notes__line {
    flex: 1; margin-left: 6px; height: 2px;
    background-image: radial-gradient(circle, var(--ink) 1px, transparent 1.3px);
    background-size: 4px 2px; background-repeat: repeat-x;
  }
  .notes__row--date .notes__line { margin-left: 20px; }
</style>
</head>
<body>

  <section class="card card--front" aria-label="Business card front">
    <div class="brand">
      <div class="brand__name">Ridgeworth Rentals LLC</div>
      <div class="brand__tagline">Providing clean, safe, and affordable housing</div>
    </div>
    <div class="front__band">
      <h1 class="holder__name">Brent Kovalich</h1>
      <p class="holder__address">12345, Address Goes Here<br>Country Name, 123456</p>
      <ul class="contact">
        <li class="contact__item">
          <svg class="contact__icon" viewBox="0 0 24 24" aria-hidden="true"><path d="M6.6 10.8c1.4 2.8 3.8 5.1 6.6 6.6l2.2-2.2c.3-.3.7-.4 1-.2 1.1.4 2.3.6 3.6.6.6 0 1 .4 1 1V20c0 .6-.4 1-1 1C10.6 21 3 13.4 3 4c0-.6.4-1 1-1h3.5c.6 0 1 .4 1 1 0 1.3.2 2.5.6 3.6.1.3 0 .7-.2 1l-2.3 2.2z"/></svg>
          480-555-3174
        </li>
        <li class="contact__item">
          <svg class="contact__icon" viewBox="0 0 24 24" aria-hidden="true"><path d="M2 5h20v14H2z M2 5l10 8 10-8" fill="none" stroke="#fff" stroke-width="0"/><path d="M2 6v13h20V6l-10 7.5z"/><path d="M2.5 4.5h19L12 11.5z"/></svg>
          brentkovalich@ridgeworthrentals.example
        </li>
        <li class="contact__item">
          <svg class="contact__icon" viewBox="0 0 24 24" aria-hidden="true"><circle cx="12" cy="12" r="10"/><path d="M7 8c2 0 3 1 3 3s2 2 2 4-1 3-1 5" fill="none" stroke="#00b6cd" stroke-width="1.8"/><path d="M15 4c0 2 2 3 4 3" fill="none" stroke="#00b6cd" stroke-width="1.8"/></svg>
          www.ridgeworthrentals.example
        </li>
      </ul>
    </div>
  </section>

  <section class="card card--back" aria-label="Business card back">
    <div class="back__band back__band--top"></div>
    <div class="notes">
      <div class="notes__row notes__row--date"><span class="notes__label">Visited Date:</span><span class="notes__line"></span></div>
      <div class="notes__row"><span class="notes__label">Interets:</span><span class="notes__line"></span></div>
      <div class="notes__row"><span class="notes__label">Problems:</span><span class="notes__line"></span></div>
    </div>
    <div class="back__band back__band--bottom"></div>
  </section>

</body>
</html>
```